Flyer design for retail store owners

i would need to have a flyer design for my retail shop customers to show that I am a mailbox store that has all major shipping vendors to for their shipping needs. Ensuring that they can take advantage of opening a house account at the store and billed monthly, word document has all the details. Please use stock images for the notary public, passport photos, mailbox brass pictures of my actual mailboxes are listed in the pictures. I need to make it POP and WOW these retail store owners as I am using it to advertise the business

```html
<!DOCTYPE html>
<html lang="en">
<head>
<meta charset="UTF-8">
<title>Private Mailbox Flyer</title>
<link href="https://fonts.googleapis.com/css2?family=Montserrat:wght@300;400;500;600;700;800&display=swap" rel="stylesheet">
<style>
  :root {
    --navy: #0d2540;
    --orange: #e8782a;
    --orange-deep: #f2551f;
    --paper-grey: #ececec;
    --white: #ffffff;
    --backdrop: #dcdcdc;
    --photo-warm-a: #b98a4a;
    --photo-warm-b: #5b4a3a;
    --photo-cool-a: #e6e1dc;
    --photo-cool-b: #7a2a2a;
  }
  * { box-sizing: border-box; margin: 0; padding: 0; }
  html, body {
    width: 1200px; height: 800px; overflow: hidden;
    background: var(--backdrop);
    font-family: "Montserrat", sans-serif;
  }
  .canvas { position: relative; width: 1200px; height: 800px; }
  .flyer {
    position: absolute; top: 84px; width: 452px; height: 634px;
    background: var(--navy); overflow: hidden;
    box-shadow: 0 6px 18px rgba(0,0,0,.25);
  }
  .flyer--front { left: 121px; }
  .flyer--back { left: 626px; }
  .flyer__art { position: absolute; inset: 0; }

  /* Front */
  .headline {
    position: absolute; right: 28px; top: 200px; text-align: right;
    color: var(--white); line-height: 1.08;
  }
  .headline__lead { font-size: 29px; font-weight: 700; display: block; }
  .headline__main { font-size: 31px; font-weight: 800; letter-spacing: 1px; display: block; }

  .section-title {
    color: var(--white); font-weight: 700; font-size: 15px;
    display: inline-block; border-bottom: 1.5px solid var(--white);
    padding-bottom: 1px; letter-spacing: .3px;
  }
  .offer { position: absolute; left: 28px; top: 268px; width: 180px; }
  .offer__text {
    margin-top: 7px; color: var(--white); font-size: 9.5px; font-weight: 400;
    line-height: 11.5px;
  }
  .about { position: absolute; right: 28px; top: 296px; width: 182px; text-align: right; }
  .about__text {
    margin-top: 8px; color: var(--white); font-size: 7.7px; line-height: 10.3px; font-weight: 400;
  }
  .deals-title {
    position: absolute; left: 28px; top: 443px; color: var(--white);
    font-size: 9.6px; font-weight: 700; letter-spacing: .2px;
  }
  .deals {
    position: absolute; left: 31px; top: 474px; width: 304px; list-style: none;
    color: var(--white); font-size: 9.3px; line-height: 11.5px; font-weight: 400;
  }
  .deals li { position: relative; padding-left: 13px; margin-bottom: 6.5px; }
  .deals li::before {
    content: ""; position: absolute; left: 0; top: 2px; width: 7px; height: 7px;
    border-radius: 50%; background: var(--white); border: 2px solid var(--navy);
  }
  .deals li.deals__narrow { width: 252px; }
  .deals strong { font-weight: 700; }
  .badge__text {
    position: absolute; left: 316px; top: 503px; width: 120px; text-align: center;
    color: var(--white); transform: rotate(-8deg); line-height: 1.2;
  }
  .badge__line1 { display: block; font-size: 7.8px; font-weight: 700; }
  .badge__line2 { display: block; font-size: 7.2px; font-weight: 600; font-style: italic; }
  .badge__line3 { display: block; font-size: 12px; font-weight: 800; }

  /* Back */
  .mission {
    position: absolute; left: 34px; right: 34px; top: 272px; text-align: center;
    color: var(--white); font-size: 12.6px; line-height: 16px; font-weight: 400;
  }
  .partners {
    position: absolute; left: 0; right: 0; top: 429px; height: 106px;
    background: var(--paper-grey); text-align: center;
  }
  .partners__title {
    margin-top: 13px; display: inline-block; color: var(--navy); font-size: 13px;
    font-weight: 600; letter-spacing: .4px; padding-bottom: 2px; position: relative;
    border-bottom: 1px solid var(--navy);
  }
  .partners__title::after {
    content: ""; position: absolute; left: 50%; bottom: -2px; width: 56px; height: 3px;
    transform: translateX(-50%); background: var(--orange);
  }
  .partners__list {
    display: flex; justify-content: center; align-items: center; gap: 11px;
    margin-top: 26px; list-style: none;
  }
  .partner {
    display: flex; align-items: center; gap: 5px;
    color: var(--navy); font-size: 10px; font-weight: 700;
  }
  .partner__mark { width: 9px; height: 9px; background: var(--orange); }
  .contact { position: absolute; left: 0; right: 0; top: 555px; height: 60px; }
  .contact__block { position: absolute; top: 0; color: var(--white); }
  .contact__block--address { left: 28px; }
  .contact__block--phone { left: 267px; }
  .contact__label {
    font-size: 14px; font-weight: 700; display: inline-block;
    border-bottom: 1.5px solid var(--white); padding-bottom: 0;
  }
  .contact__value { font-size: 14px; font-weight: 400; margin-top: 5px; letter-spacing: .2px; }
  .contact__divider {
    position: absolute; left: 227px; top: -8px; width: 1.5px; height: 52px; background: var(--orange);
  }
</style>
</head>
<body>
<div class="canvas">

  <section class="flyer flyer--front">
    <svg class="flyer__art" width="452" height="634" viewBox="0 0 452 634">
      <defs>
        <linearGradient id="mailboxTones" x1="0" y1="0" x2="1" y2="1">
          <stop offset="0" stop-color="#f1c36a"/>
          <stop offset=".35" stop-color="var(--photo-warm-a)"/>
          <stop offset="1" stop-color="var(--photo-warm-b)"/>
        </linearGradient>
        <linearGradient id="orangeSweep" x1="0" y1="0" x2="0" y2="1">
          <stop offset="0" stop-color="#e07424"/>
          <stop offset="1" stop-color="#ec8a3a"/>
        </linearGradient>
      </defs>
      <path d="M399,0 H452 V287 H330 C255,286 200,250 170,195 C290,190 385,110 399,0 Z" fill="url(#orangeSweep)"/>
      <path role="img" aria-label="Photo of numbered brass private mailboxes with mail in one slot"
            d="M0,0 H399 C385,110 290,190 170,195 H0 Z" fill="url(#mailboxTones)"/>
      <path d="M399,0 C385,110 290,190 170,195 H0" fill="none" stroke="var(--white)" stroke-width="1.2"/>
      <rect x="0" y="464" width="452" height="170" fill="var(--orange)"/>
      <g class="badge-shape">
        <g stroke="var(--orange-deep)" stroke-width="1" opacity=".8">
          <line x1="374" y1="527" x2="432" y2="470"/><line x1="374" y1="527" x2="450" y2="540"/>
          <line x1="374" y1="527" x2="420" y2="600"/><line x1="374" y1="527" x2="330" y2="605"/>
          <line x1="374" y1="527" x2="305" y2="560"/><line x1="374" y1="527" x2="318" y2="470"/>
        </g>
        <polygon points="346,474 408,480 434,520 420,578 360,590 322,556 318,500" fill="var(--navy)"/>
        <polygon points="350,482 404,470 432,510 425,566 372,584 330,562 322,508" fill="var(--orange-deep)"/>
        <polygon points="356,492 400,484 420,515 414,558 374,572 340,556 334,512" fill="none"
                 stroke="var(--white)" stroke-width=".8" stroke-dasharray="10 5"/>
      </g>
    </svg>

    <h1 class="headline">
      <span class="headline__lead">Need a Private</span>
      <span class="headline__main">MAILBOX?</span>
    </h1>

    <div class="offer">
      <h2 class="section-title">WE OFFER:</h2>
      <p class="offer__text">Now renting mailboxes on Maplewood Commons Shopping Center. We are offering all Maplewood Commons shopping center owners/employees an exclusive promo deal! $12 a month for 6-12 months leases! You get a mailbox in the shop, a book of stamps(20 count), 3 notarizations by appointment, 100 copies of black and white, and 100 copies of color. Please see associate for sign up!</p>
    </div>

    <div class="about">
      <h2 class="section-title">ABOUT US:</h2>
      <p class="about__text">Renting a mail box is one of the most efficient and cost saving methods for receiving your mail and packages. Instead of having to worry about private security, weather conditions, sorting, and deliveries; all you have to do is pick-up your mail from our secured facility each day except Sundays. You will get a notification when mail arrives whether envelope or package, it will be scanned in daily which other mailbox stores do not offer! We offer onsite Notary Public with no appointments and onsite Passport Photos and can ship out same day.</p>
    </div>

    <h3 class="deals-title">CHECK OUT THESE OTHER DEALS!</h3>
    <ul class="deals">
      <li class="deals__narrow">As a retail owner, you know how important it is to keep your customers coming back - you will get <strong>20%</strong> discount for printing services.</li>
      <li class="deals__narrow">We duplicate keys for $2/each, our regular price charge is $4/each. Save up to <strong>50%</strong>!</li>
      <li class="deals__narrow">Lamination is also discounted at <strong>10%</strong> off.</li>
      <li class="deals__narrow"><strong>10%</strong> off retail supplies ... must be minimum of 10$</li>
      <li>For house accounts -a 5% discount will be deducted monthly of billing change to invoicing PLUS we're giving another 5% of the discount if you upgrade and sign up for mailbox. <strong>Great right?</strong></li>
    </ul>

    <p class="badge__text">
      <span class="badge__line1">TAKE ADVANTAGE</span>
      <span class="badge__line2">Of This Limited Time</span>
      <span class="badge__line3">OFFER NOW!</span>
    </p>
  </section>

  <section class="flyer flyer--back">
    <svg class="flyer__art" width="452" height="634" viewBox="0 0 452 634">
      <defs>
        <linearGradient id="notaryTones" x1="0" y1="0" x2="1" y2="1">
          <stop offset="0" stop-color="var(--photo-cool-b)"/>
          <stop offset=".4" stop-color="var(--photo-cool-a)"/>
          <stop offset=".75" stop-color="#d9d3cc"/>
          <stop offset="1" stop-color="#1f2f63"/>
        </linearGradient>
      </defs>
      <path role="img" aria-label="Photo of a notary public stamp, wax seal, certificate and passport with boarding passes"
            d="M0,0 H452 V240 H216 C120,236 30,200 0,150 Z" fill="url(#notaryTones)"/>
      <path d="M0,150 C30,200 120,236 216,240 H452" fill="none" stroke="var(--orange)" stroke-width="2"/>
    </svg>

    <p class="mission">At Swift Parcel Hub, our goal is to make your shipping experience as convenient as possible. Whether you are shipping packages, documents, or packages, we are here to help. Whether you want to track your package or estimate the price of your package, it is easy for you. We are ready to handle all of your postal services! Get also the services you need; printing, copying, and stop in to purchase postage or shipping materials</p>

    <div class="partners">
      <h2 class="partners__title">SERVICE POINT PARTNERS</h2>
      <ul class="partners__list">
        <li class="partner"><span class="partner__mark"></span>Northwind Freight</li>
        <li class="partner">Parcelway</li>
        <li class="partner">National Post</li>
        <li class="partner">Skyline Express</li>
      </ul>
    </div>

    <div class="contact">
      <div class="contact__block contact__block--address">
        <h3 class="contact__label">Our address:</h3>
        <p class="contact__value">Lorem Ipsum is simpl</p>
      </div>
      <span class="contact__divider"></span>
      <div class="contact__block contact__block--phone">
        <h3 class="contact__label">Phone:</h3>
        <p class="contact__value">00 555 01427</p>
      </div>
    </div>
  </section>

</div>
</body>
</html>
```